Flyer for the Lumen 2025 Conference

I am looking to produce a flyer for our upcoming conference, Lumen 2025. This is an annual conference that we plan to publicize on social media. The ideal designer will create a flyer that is eye-catching and effectively communicates the key information. Please see attached our logo, speaker photo, and flyer content.

Target Market(s)

All demographics

Industry/Entity Type

Christian

Font styles to use
Sans Serif

Requirements
Should not have
• Cross, church

```html
<!DOCTYPE html>
<html lang="en">
<head>
<meta charset="utf-8">
<title>Lumen 2025 Conference</title>
<link rel="stylesheet" href="https://fonts.googleapis.com/css2?family=Anton&family=Great+Vibes&family=Montserrat:wght@600;700;800;900&family=Poppins:wght@400;500&display=swap">
<style>
  :root{
    --navy-deep:#0d0f3d;
    --navy:#1a1f6b;
    --ink:#1b1d55;
    --orange:#ff9a00;
    --yellow:#ffd21a;
    --gold:#ffc20e;
    --teal:#19b7c6;
    --white:#ffffff;
    --rule:#b07a2a;
  }
  *{box-sizing:border-box;margin:0;padding:0}
  html,body{width:973px;height:1200px;overflow:hidden;background:#fff}
  .flyer{position:relative;width:973px;height:1200px;overflow:hidden;
    background:radial-gradient(ellipse at 20% 10%, #23307f 0%, var(--navy) 25%, var(--navy-deep) 75%);
    font-family:'Montserrat',sans-serif;color:var(--white)}
  .abs{position:absolute}

  .brand{left:82px;top:118px;display:flex;align-items:center;gap:14px}
  .brand-dot{width:22px;height:22px;border-radius:50%;background:var(--orange)}
  .brand-name{font-family:'Montserrat',sans-serif;font-weight:700;font-size:46px;letter-spacing:2px;color:var(--white)}

  .speaker-photo{left:0;top:252px;width:450px;height:760px;
    background:radial-gradient(ellipse at 50% 40%, #2f7fd6 0%, #1d5cb4 45%, rgba(20,40,110,0) 75%)}

  .title{left:386px;top:140px;font-family:'Anton',sans-serif;font-size:182px;line-height:1;letter-spacing:-2px;
    transform:scaleX(0.9);transform-origin:left top;
    background:linear-gradient(180deg,var(--yellow) 0%,var(--orange) 90%);-webkit-background-clip:text;background-clip:text;color:transparent}
  .year{left:824px;top:148px;font-family:'Anton',sans-serif;font-size:82px;line-height:.95;text-align:left}
  .year .top{color:#eceef4;display:block}
  .year .bottom{color:var(--teal);display:block}

  .script{left:379px;top:300px;font-family:'Great Vibes',cursive;font-size:70px;color:var(--white);line-height:1}
  .tag-conf{left:688px;top:330px;width:204px;height:48px;background:linear-gradient(90deg,var(--orange),var(--yellow));
    color:var(--ink);font-weight:900;font-size:25px;display:flex;align-items:center;justify-content:center;letter-spacing:.5px}

  .topic{left:389px;top:404px;height:39px;display:flex}
  .topic-label{width:97px;background:linear-gradient(90deg,var(--orange),var(--yellow));color:var(--ink);
    font-weight:900;font-size:22px;display:flex;align-items:center;justify-content:center}
  .topic-text{margin-left:5px;width:404px;border:1px solid var(--orange);border-radius:0 8px 8px 0;
    font-weight:800;font-size:21px;letter-spacing:5px;display:flex;align-items:center;justify-content:center}

  .session{left:466px;width:430px;height:84px}
  .session-date{position:absolute;left:0;top:0;width:294px;height:84px;border:1px solid var(--rule);border-radius:12px;
    display:flex;align-items:center;justify-content:center;font-family:'Anton',sans-serif;font-size:42px;letter-spacing:-.5px}
  .session-date .day{color:var(--gold)}
  .session-day{position:absolute;left:0;width:294px;top:-13px;text-align:center;font-weight:800;font-size:19px;letter-spacing:7px;line-height:24px}
  .session-day span{background:#141755;padding:0 8px}
  .session-time{position:absolute;left:294px;top:14px;width:122px;height:56px;background:var(--teal);
    display:flex;flex-direction:column;font-weight:800;font-size:18px;color:var(--white)}
  .session-time span{flex:1;display:flex;align-items:center;justify-content:center}
  .session-time span+span{border-top:1.5px solid #0d6d85}
  .session-to{position:absolute;left:406px;top:30px;width:24px;height:24px;border-radius:50%;background:var(--gold);
    color:var(--ink);font-size:9px;font-weight:900;display:flex;align-items:center;justify-content:center}

  .location{left:466px;top:804px}
  .location-head{display:flex;align-items:center;gap:8px;color:var(--gold);font-weight:900;font-size:26px}
  .venue{margin-top:10px;color:var(--teal);font-weight:900;font-size:22px;line-height:27px}
  .address{margin-top:8px;font-family:'Poppins',sans-serif;font-size:18px;line-height:24px;color:#f1f1f6}

  .footer-edge{left:0;top:975px}
  .footer{left:0;top:992px;width:973px;height:208px;background:var(--white);color:var(--ink)}
  .speaker-tab{left:80px;top:28px;width:44px;height:114px;border-radius:8px;background:linear-gradient(180deg,var(--gold),var(--orange));
    display:flex;align-items:center;justify-content:center}
  .speaker-tab span{transform:rotate(-90deg);font-weight:900;font-size:19px;color:var(--ink);letter-spacing:1px}
  .speaker-name{left:140px;top:32px}
  .speaker-name .role{font-weight:900;font-size:23px;letter-spacing:6px}
  .speaker-name .name{font-weight:900;font-size:35px;line-height:40px}
  .divider{top:45px;width:1px;height:106px;background:#9aa0c0}
  .contacts{left:384px;top:44px;display:flex;flex-direction:column;gap:8px}
  .contact{display:flex;align-items:center;gap:14px;font-weight:700;font-size:16px}
  .contact.phone{font-size:24px;font-weight:800}
  .contact-icon{width:22px;height:22px;border-radius:50%;background:var(--gold);display:flex;align-items:center;justify-content:center}
  .app{left:656px;top:44px;font-weight:800;font-size:15px;line-height:19px}
  .app .hl{color:var(--orange);font-size:18px}
  .badge{top:94px;width:119px;height:38px;border:1px solid #9aa0b8;border-radius:5px;background:#f4f5f8}
</style>
</head>
<body>
<main class="flyer">
  <div class="abs brand"><span class="brand-dot"></span><span class="brand-name">HALVEN</span></div>

  <div class="abs speaker-photo" role="img" aria-label="Portrait of the speaker in a blue suit, seated"></div>

  <h1 class="abs title">LUMEN</h1>
  <div class="abs year"><span class="top">20</span><span class="bottom">25</span></div>

  <div class="abs script">A Prophetic</div>
  <div class="abs tag-conf">CONFERENCE</div>

  <div class="abs topic">
    <div class="topic-label">TOPIC</div>
    <div class="topic-text">THE VOICE OF THE LORD</div>
  </div>

  <section class="abs session" style="top:494px">
    <div class="session-date">December&nbsp;<span class="day">26th</span></div>
    <div class="session-day"><span>FRIDAY</span></div>
    <div class="session-time"><span>6:30PM</span><span>9:00PM</span></div>
    <div class="session-to">TO</div>
  </section>
  <section class="abs session" style="top:598px">
    <div class="session-date">December&nbsp;<span class="day">27th</span></div>
    <div class="session-day"><span>SATURDAY</span></div>
    <div class="session-time"><span>5:30PM</span><span>8:00PM</span></div>
    <div class="session-to">TO</div>
  </section>
  <section class="abs session" style="top:702px">
    <div class="session-date">December&nbsp;<span class="day">29th</span></div>
    <div class="session-day"><span>SUNDAY</span></div>
    <div class="session-time"><span>4:30PM</span><span>7:00PM</span></div>
    <div class="session-to">TO</div>
  </section>

  <section class="abs location">
    <div class="location-head">
      <svg width="22" height="26" viewBox="0 0 22 26"><path d="M11 2a7 7 0 0 1 7 7c0 5-7 11-7 11S4 14 4 9a7 7 0 0 1 7-7z" fill="none" stroke="#ffc20e" stroke-width="2.5"/><circle cx="11" cy="9" r="2.5" fill="#ffc20e"/><path d="M2 24h18" stroke="#ffc20e" stroke-width="2.5"/></svg>
      LOCATION
    </div>
    <div class="venue">THE RIVERSIDE PERFORMING<br>ARTS CENTER</div>
    <div class="address">128 Meadowlane Street<br>Riverside, Maine 04000</div>
  </section>

  <svg class="abs footer-edge" width="973" height="20" viewBox="0 0 973 20" aria-hidden="true">
    <polygon fill="#ffffff" points="0,14 40,10 80,15 130,9 190,13 240,8 300,14 360,10 420,15 480,9 540,13 600,8 660,14 720,10 780,15 840,9 900,13 973,8 973,20 0,20"/>
  </svg>

  <footer class="abs footer">
    <div class="abs speaker-tab"><span>SPEAKER</span></div>
    <div class="abs speaker-name">
      <div class="role">PROPHET</div>
      <div class="name">ELIAS<br>MARLOWE</div>
    </div>
    <div class="abs divider" style="left:362px"></div>
    <div class="contacts abs">
      <div class="contact phone"><span class="contact-icon"><svg width="12" height="12" viewBox="0 0 12 12"><path d="M2 1l2 0 1 3-1.5 1a6 6 0 0 0 3.5 3.5L8 7l3 1v2a1 1 0 0 1-1 1A9 9 0 0 1 1 2a1 1 0 0 1 1-1z" fill="#1b1d55"/></svg></span>207 555 0142</div>
      <div class="contact"><span class="contact-icon"><svg width="12" height="10" viewBox="0 0 12 10"><rect x="1" y="1" width="10" height="8" fill="none" stroke="#1b1d55" stroke-width="1.4"/><path d="M1 1l5 4 5-4" fill="none" stroke="#1b1d55" stroke-width="1.4"/></svg></span>contact@halven.org</div>
      <div class="contact"><span class="contact-icon"><svg width="12" height="12" viewBox="0 0 12 12"><circle cx="6" cy="6" r="5" fill="none" stroke="#1b1d55" stroke-width="1.3"/><path d="M1 6h10M6 1c-2 3-2 7 0 10M6 1c2 3 2 7 0 10" fill="none" stroke="#1b1d55" stroke-width="1.1"/></svg></span>www.halven.org</div>
    </div>
    <div class="abs divider" style="left:626px"></div>
    <div class="abs app">Download the <span class="hl">HALVEN App</span><br>to stay updated on the event</div>
    <div class="abs badge" style="left:651px"></div>
    <div class="abs badge" style="left:776px"></div>
  </footer>
</main>
</body>
</html>
```